Business Cards for new orthopaedic surgery practice

My husband and I are starting our own orthopaedic surgery practice. We are looking for a business card that is uniform, but one will have my name/title and the other will have his. You can just create one design with my name on it for now. But when I choose your design as the winning design I will ask that you add another copy with his name/title.

We are looking for classy, simple, elite all in one. We like dark blues/a little gold/yellow. Something that goes with our logo. We want our logo incorporated. Here is all the info you need:
Business name: RV Bone & Vitality Center
Location: 38517 North Willowmere Ave
Maple Harbor, GA 30518
Phone: 954-218-4063
Fax: 954-582-7341
Email: info@myrvbonecare.example

Names: Lydia Vance, M.D.
Board Certified Hand and Upper Extremity Surgeon

Ebo Dansu, M.D.
Board Certified Hip & Knee Replacement/General Orthopaedic Surgeon

Can decide what you want to put on the back. Maybe a slogan:
Steady Hands. Centered on You

I am just going to upload our logo. The only thing is if we select you as the winning design, the location, and phone numbers may change. We will need your help to update that once fully solidified.

Industry/Entity Type

Medical

Contact Information for Business Card

Colors
0054AA
0677BA
7BADD7
CADEEF
E8F1F8
0094D4
00A9DD
6FCCEA
C7EBF8
E9F6FB

Requirements
Must have
• class, appeal,
Should not have
• We want to air on the side of masculine if we are looking at masculine vs. feminine feel. But we still want it classy, sophisticated, and something we will love

```html
<!DOCTYPE html>
<html lang="en">
<head>
<meta charset="UTF-8">
<title>RV Bone &amp; Vitality Center – Business Card</title>
<link href="https://fonts.googleapis.com/css2?family=Montserrat:wght@300;400;500;600&display=swap" rel="stylesheet">
<style>
  :root {
    --backdrop: #e1e1e1;
    --navy: #2c3e80;
    --deep-blue: #1d3c84;
    --cyan: #00bde0;
    --white: #ffffff;
    --grey-text: #6f6f6f;
    --body-text: #555555;
    --rule: #a8a8a8;
  }
  * { margin: 0; padding: 0; box-sizing: border-box; }
  html, body {
    width: 1200px; height: 1200px; overflow: hidden;
    background: var(--backdrop);
    font-family: "Montserrat", sans-serif;
  }
  .card {
    position: absolute;
    left: 179px;
    width: 861px;
    height: 496px;
    overflow: hidden;
  }
  /* Front */
  .card-front { top: 84px; background: var(--navy); color: var(--white); }
  .front-brand {
    position: absolute; left: 0; right: 0; top: 238px;
    text-align: center;
    font-size: 44px; font-weight: 500; letter-spacing: 0.5px;
    color: var(--white);
  }
  .front-slogan {
    position: absolute; left: 0; right: 0; top: 440px;
    text-align: center;
    font-size: 27px; font-weight: 300; letter-spacing: 0.3px;
  }
  /* Back */
  .card-back { top: 622px; background: var(--white); }
  .back-brand {
    position: absolute; left: 45px; top: 92px;
    display: flex; align-items: center; gap: 16px;
    font-size: 32px; font-weight: 500; color: var(--deep-blue);
  }
  .back-brand .mark {
    width: 22px; height: 22px; background: var(--deep-blue);
  }
  .name-accent {
    position: absolute; left: 0; top: 277px; width: 9px; height: 59px;
    background: var(--deep-blue);
  }
  .doctor-name {
    position: absolute; left: 44px; top: 272px;
    font-size: 35px; font-weight: 600; color: var(--deep-blue);
  }
  .doctor-title {
    position: absolute; left: 44px; top: 318px;
    font-size: 25px; font-weight: 500; color: var(--grey-text);
  }
  .divider {
    position: absolute; left: 44px; top: 348px; width: 776px; height: 1.5px;
    background: var(--rule);
  }
  .contact-list {
    position: absolute; left: 44px; top: 354px; list-style: none;
  }
  .contact-list li {
    display: flex; align-items: center; height: 37.5px;
    font-size: 26px; font-weight: 400; color: var(--body-text); letter-spacing: 0.5px;
  }
  .contact-list svg { width: 24px; height: 22px; margin-right: 13px; fill: var(--deep-blue); }
  .address {
    position: absolute; right: 41px; top: 358px; text-align: right;
    font-size: 26px; line-height: 31px; font-weight: 400; color: var(--body-text); letter-spacing: 0.5px;
    font-style: normal;
  }
  .band-cyan {
    position: absolute; left: 0; bottom: 0; width: 480px; height: 15px;
    background: var(--cyan);
  }
  .band-navy {
    position: absolute; right: 0; bottom: 0; width: 400px; height: 31px;
  }
</style>
</head>
<body>
  <section class="card card-front">
    <div class="front-brand">RV Bone &amp; Vitality Center</div>
    <p class="front-slogan">Steady Hands. Centered on You</p>
  </section>

  <section class="card card-back">
    <div class="back-brand"><span class="mark"></span>RV Bone &amp; Vitality Center</div>

    <span class="name-accent"></span>
    <h1 class="doctor-name">Lydia Vance, M.D.</h1>
    <p class="doctor-title">Board Certified Hand and Upper Extremity Surgeon</p>
    <span class="divider"></span>

    <ul class="contact-list">
      <li>
        <svg viewBox="0 0 24 24" aria-hidden="true"><path d="M6.6 10.8a15.2 15.2 0 0 0 6.6 6.6l2.2-2.2a1 1 0 0 1 1-.25 11.4 11.4 0 0 0 3.6.57 1 1 0 0 1 1 1V20a1 1 0 0 1-1 1A17 17 0 0 1 3 4a1 1 0 0 1 1-1h3.5a1 1 0 0 1 1 1c0 1.25.2 2.45.57 3.57a1 1 0 0 1-.25 1z"/></svg>
        954-218-4063
      </li>
      <li>
        <svg viewBox="0 0 24 24" aria-hidden="true"><path d="M6 2h12v5H6z"/><path d="M3 8h18v9h-3v-3H6v3H3z"/><path d="M7 15h10v7H7z"/></svg>
        954-582-7341
      </li>
      <li>
        <svg viewBox="0 0 24 24" aria-hidden="true"><path d="M2 5h20v14H2z" fill="none" stroke="#1d3c84" stroke-width="2"/><path d="M2 5l10 8 10-8M2 19l7-7M22 19l-7-7" fill="none" stroke="#1d3c84" stroke-width="2"/></svg>
        info@myrvbonecare.example
      </li>
    </ul>

    <address class="address">38517 North Willowmere Ave<br>Maple Harbor, GA 30518</address>

    <span class="band-cyan"></span>
    <svg class="band-navy" viewBox="0 0 400 31" preserveAspectRatio="none" aria-hidden="true">
      <polygon points="20,0 400,0 400,31 0,31" fill="#1d3c84"/>
    </svg>
  </section>
</body>
</html>
```